Business card design Needed for new logo / Construction business, home extensions and new builds

We need a business card design using our new logo files which i will attach to this project :)

We are a small construction business specialising in home extensions, new builds and property development. We are very ambitious and would appreciate professional and elegant designs for our new business card.

Very serious about using the services on MakerQuarry and recently acquired our new logo from here :)

Please get involved, i will feedback when i can as i am very busy but can respond daily, thanks

Target Market(s)

People that want to build onto their houses, new building developments or adding too their existing property

Industry/Entity Type

Construction

Contact Information for Business Card

Renwick Tolliver Construction, Lionel Ashby (Managing Director), Tel 07822254961, email - info@renwick-tolliver, www.renwick-tolliver.co.uk

Colors

Designer to choose colors to be used in the design.

Requirements
Must have
• I like a deep grey on the back please. A lot of you have provided black from and back, try mixing things up a little. The black looks cool 😎 Thanks

```html
<!DOCTYPE html>
<html lang="en">
<head>
<meta charset="utf-8">
<title>Renwick Tolliver Construction – Business Card</title>
<link rel="stylesheet" href="https://fonts.googleapis.com/css2?family=Open+Sans:wght@400;600;700&display=swap">
<style>
  :root {
    --stage: #1b1b1d;
    --card-black: #1f1f22;
    --card-grey-light: #a3a8ad;
    --card-grey-dark: #7f848a;
    --gold: #e0a52a;
    --gold-deep: #b8861f;
    --white: #f4f4f4;
    --silver: #c9ccd0;
  }
  * { box-sizing: border-box; margin: 0; padding: 0; }
  html, body {
    width: 1200px; height: 780px; overflow: hidden;
    background: var(--stage);
    font-family: "Open Sans", Arial, sans-serif;
  }
  .canvas { position: relative; width: 1200px; height: 780px; }

  .card {
    position: absolute;
    width: 540px; height: 330px;
    border-radius: 22px;
    overflow: hidden;
  }

  /* Back of card */
  .card-back {
    left: 50px; top: 80px;
    border: 2px solid var(--gold);
  }
  .card-back .pattern-fill {
    position: absolute; inset: 0;
    background: linear-gradient(160deg, var(--card-grey-light) 0%, var(--card-grey-dark) 100%);
  }
  .card-back .back-lockup {
    position: absolute; top: 26px; right: 30px;
    display: flex; align-items: center; gap: 6px;
    font-size: 8px; font-weight: 600; color: var(--white);
    letter-spacing: 0.04em;
  }
  .back-lockup .mark-square { width: 12px; height: 12px; background: var(--white); }

  /* Front of card */
  .card-front {
    left: 610px; top: 370px;
    background: var(--card-black);
    border: 2px solid var(--gold);
    color: var(--white);
  }
  .brand {
    position: absolute; left: 34px; top: 44px;
    display: flex; align-items: center; gap: 10px;
  }
  .brand .mark-square { width: 40px; height: 40px; background: var(--gold); }
  .brand .company-name {
    font-size: 15px; font-weight: 600; line-height: 1.25;
    color: var(--silver); letter-spacing: 0.08em; text-transform: uppercase;
    width: 200px;
  }
  .address {
    position: absolute; left: 34px; top: 130px;
    font-size: 13px; line-height: 1.5; color: var(--white);
  }
  .contacts {
    position: absolute; left: 34px; bottom: 34px;
    list-style: none; font-size: 13px; line-height: 1.7;
  }
  .contacts li { display: flex; align-items: center; gap: 10px; }
  .contacts svg { width: 13px; height: 13px; flex: none; }

  .person {
    position: absolute; right: 42px; top: 52px; text-align: right;
  }
  .person .name { font-size: 26px; font-weight: 700; color: var(--white); }
  .person .name .surname { color: var(--gold); }
  .person .role { font-size: 13px; font-weight: 600; color: var(--white); margin-top: 2px; }
  .gold-tab {
    position: absolute; right: 0; top: 50px;
    width: 22px; height: 62px;
    background: linear-gradient(90deg, var(--gold-deep), var(--gold));
  }
</style>
</head>
<body>
<main class="canvas">

  <section class="card card-back" aria-label="Business card back">
    <div class="pattern-fill" role="img" aria-label="Repeating pattern of the company monogram on deep grey"></div>
    <div class="back-lockup">
      <span class="mark-square"></span>
      <span>Renwick Tolliver Construction</span>
    </div>
  </section>

  <section class="card card-front" aria-label="Business card front">
    <div class="brand">
      <span class="mark-square"></span>
      <span class="company-name">Renwick Tolliver Construction</span>
    </div>

    <p class="address">Harrow Lane, Elmsfield<br>Westbourne, WB4 7KT</p>

    <ul class="contacts">
      <li>
        <svg viewBox="0 0 24 24" fill="var(--gold)"><path d="M6.6 10.8a15 15 0 0 0 6.6 6.6l2.2-2.2c.3-.3.7-.4 1-.2 1.1.4 2.3.6 3.6.6.6 0 1 .4 1 1V20c0 .6-.4 1-1 1A17 17 0 0 1 3 4c0-.6.4-1 1-1h3.5c.6 0 1 .4 1 1 0 1.3.2 2.5.6 3.6.1.3 0 .7-.2 1z"/></svg>
        <span>0782 225 4961</span>
      </li>
      <li>
        <svg viewBox="0 0 24 24" fill="none" stroke="var(--gold)" stroke-width="2"><rect x="3" y="5" width="18" height="14" rx="2"/><path d="M3 7l9 6 9-6"/></svg>
        <span>info@renwick-tolliver.co.uk</span>
      </li>
      <li>
        <svg viewBox="0 0 24 24" fill="none" stroke="var(--gold)" stroke-width="2"><circle cx="12" cy="12" r="9"/><path d="M3 12h18M12 3c3 3 3 15 0 18M12 3c-3 3-3 15 0 18"/></svg>
        <span>www.renwick-tolliver.co.uk</span>
      </li>
    </ul>

    <div class="person">
      <p class="name">Lionel <span class="surname">Ashby</span></p>
      <p class="role">Managing Director</p>
    </div>
    <span class="gold-tab"></span>
  </section>

</main>
</body>
</html>
```